Kelo Wave Mint Business cards

Logo, tag line and photo on card
Agent Name
Title
Address
Phone number
Email
Website
Make logo on one side large by rotating  to portrait format.  Keep the background of the logo white.

Contact Information for Business Card
Slogan; Making Every Wave Count

```html
<!DOCTYPE html>
<html lang="en">
<head>
<meta charset="utf-8">
<title>Kelo Wave Mint – Business Cards</title>
<link rel="stylesheet" href="https://fonts.googleapis.com/css2?family=Montserrat:wght@500;600;700;800&display=swap">
<style>
  :root {
    --navy: #23306b;
    --navy-deep: #1b2660;
    --red: #d0212b;
    --white: #ffffff;
    --stage: #a9aaac;
    --photo-light: #f4f4f4;
    --photo-mid: #8a8a8e;
  }
  * { box-sizing: border-box; margin: 0; padding: 0; }
  html, body { width: 1200px; height: 781px; overflow: hidden; }
  body {
    background: var(--stage);
    font-family: "Montserrat", sans-serif;
    position: relative;
  }
  .card {
    position: absolute;
    top: 85px;
    width: 350px;
    height: 612px;
    border-radius: 22px;
    box-shadow: 0 10px 28px rgba(0,0,0,.25);
    overflow: hidden;
  }
  .card--front {
    left: 195px;
    background: linear-gradient(160deg, var(--navy-deep) 0%, var(--navy) 60%, #2d3b7a 100%);
    color: var(--white);
    text-align: center;
  }
  .card--back {
    left: 655px;
    background: var(--white);
    display: flex;
    flex-direction: column;
    align-items: center;
  }
  .agent-name {
    margin-top: 40px;
    font-size: 22px;
    font-weight: 800;
    letter-spacing: 1px;
    color: var(--red);
    text-transform: uppercase;
  }
  .agent-title {
    margin-top: 2px;
    font-size: 16px;
    font-weight: 600;
  }
  .photo-frame {
    margin: 20px auto 0;
    width: 270px;
    height: 270px;
    border: 6px solid var(--red);
    border-radius: 26px;
    overflow: hidden;
    background: var(--white);
  }
  .photo {
    width: 100%;
    height: 100%;
    background: radial-gradient(circle at 55% 40%, var(--photo-light) 0%, #d9d9dc 45%, var(--photo-mid) 100%);
  }
  .address {
    margin-top: 24px;
    font-size: 15px;
    font-weight: 500;
    line-height: 1.45;
  }
  .contact-icons {
    display: flex;
    justify-content: center;
    gap: 10px;
    margin-top: 14px;
  }
  .contact-icons svg { width: 14px; height: 14px; }
  .contact-lines {
    margin-top: 10px;
    font-size: 15px;
    font-weight: 500;
    line-height: 1.5;
  }
  .phone { letter-spacing: 3px; }
  .brand-name {
    margin-top: 150px;
    font-size: 56px;
    font-weight: 800;
    line-height: 1.02;
    color: var(--navy);
    text-align: center;
  }
  .tagline {
    margin-top: auto;
    margin-bottom: 58px;
    font-size: 17px;
    font-weight: 600;
    color: var(--navy);
  }
</style>
</head>
<body>
  <article class="card card--front">
    <h1 class="agent-name">Marcus Delaney</h1>
    <p class="agent-title">Founder</p>
    <div class="photo-frame">
      <div class="photo" role="img" aria-label="Portrait photo of the founder"></div>
    </div>
    <p class="address">Suite 2150, 612 - 7th Avenue<br>SW, Calgary, AB, T2P 1K8</p>
    <div class="contact-icons" aria-hidden="true">
      <svg viewBox="0 0 16 16"><path fill="#d0212b" d="M4 1l2.5 3-1.5 2a9 9 0 0 0 5 5l2-1.5 3 2.5-2 2C6 15 1 10 2 3z"/></svg>
      <svg viewBox="0 0 16 16"><rect x="1" y="3" width="14" height="10" rx="1" fill="#d0212b"/><path d="M1.5 3.5L8 9l6.5-5.5" stroke="#fff" stroke-width="1.4" fill="none"/></svg>
      <svg viewBox="0 0 16 16"><circle cx="8" cy="8" r="6.5" fill="none" stroke="#d0212b" stroke-width="1.6"/><path d="M1.5 8h13M8 1.5c-3 3.5-3 9.5 0 13M8 1.5c3 3.5 3 9.5 0 13" stroke="#d0212b" stroke-width="1.2" fill="none"/></svg>
    </div>
    <p class="contact-lines">
      <span class="phone">403 555 0147</span><br>
      hello@kelowavemint.com<br>
      www.kelowavemint.com
    </p>
  </article>

  <article class="card card--back">
    <p class="brand-name">Kelo<br>Wave<br>Mint</p>
    <p class="tagline">Making Every Wave Count</p>
  </article>
</body>
</html>
```